Business Card Design Project

We are a construction company in Orange County, CA. We need a two sided business card. We would like the back to be our logo with web URL. Front should included Name, title, address, phone, fax and email address.

our address is
627 West Dorrance Blvd, Suite 308
Anaheim, CA 92718

Our logo files are attached.

Construction

```html
<!DOCTYPE html>
<html lang="en">
<head>
<meta charset="utf-8">
<title>Merido Business Card</title>
<link rel="stylesheet" href="https://fonts.googleapis.com/css2?family=Source+Sans+3:wght@400;600;700;800&display=swap">
<style>
  :root {
    --navy: #1a4b7d;
    --ink: #4a4a4a;
    --rule: #9a9a9a;
    --paper: #ffffff;
    --backdrop: #e9e6e2;
    --charcoal: #232323;
    --graphite: #8a8a8a;
  }
  * { box-sizing: border-box; margin: 0; padding: 0; }
  html, body { width: 1200px; height: 404px; overflow: hidden; }
  body {
    background: var(--backdrop);
    font-family: "Source Sans 3", Arial, sans-serif;
    position: relative;
  }
  .card {
    position: absolute;
    top: 45px;
    width: 525px;
    height: 298px;
    overflow: hidden;
    box-shadow: 0 1px 3px rgba(0,0,0,0.25);
  }
  .card--front { left: 55px; background: var(--paper); }
  .card--back { left: 611px; background: var(--navy); }

  .wordmark {
    position: absolute;
    left: 0; right: 0;
    text-align: center;
    font-weight: 800;
    font-size: 74px;
    line-height: 1;
    letter-spacing: -1px;
  }
  .card--front .wordmark { top: 38px; color: var(--navy); }
  .card--back .wordmark { top: 106px; color: var(--paper); }

  .address {
    position: absolute;
    right: 278px;
    top: 157px;
    text-align: right;
    color: var(--ink);
    font-size: 13.5px;
    font-style: normal;
    line-height: 17px;
  }
  .divider {
    position: absolute;
    left: 264px;
    top: 147px;
    width: 1px;
    height: 74px;
    background: var(--rule);
  }
  .contacts {
    position: absolute;
    left: 284px;
    top: 147px;
    list-style: none;
    color: var(--ink);
    font-size: 13.5px;
    line-height: 17.5px;
  }
  .contacts li { display: flex; align-items: center; gap: 5px; }
  .contacts svg { width: 10px; height: 10px; fill: var(--ink); flex: none; }

  .swoosh { position: absolute; left: 0; bottom: 0; width: 525px; height: 298px; }

  .holder {
    position: absolute;
    right: 62px;
    top: 249px;
    text-align: center;
    color: var(--paper);
  }
  .holder__name { font-weight: 700; font-size: 18px; line-height: 20px; }
  .holder__title { font-weight: 400; font-size: 16px; line-height: 19px; }

  .web-address {
    position: absolute;
    left: 0; right: 0;
    top: 206px;
    text-align: center;
    color: var(--paper);
    font-size: 14px;
    letter-spacing: 2.4px;
  }
</style>
</head>
<body>
  <section class="card card--front" aria-label="Business card front">
    <div class="wordmark">MERIDO</div>

    <address class="address">
      627 West Dorrance Blvd<br>
      Suite 308, Anaheim<br>
      CA&nbsp;&nbsp;92718
    </address>
    <div class="divider"></div>
    <ul class="contacts">
      <li><svg viewBox="0 0 10 10" aria-label="Phone"><path d="M2 0.5 L3.6 2.6 L2.7 3.6 C3.3 5 4.9 6.7 6.4 7.3 L7.4 6.4 L9.5 8 L8.4 9.5 C4.5 9.3 0.7 5.5 0.5 1.6 Z"/></svg>01-345-6789</li>
      <li><svg viewBox="0 0 10 10" aria-label="Fax"><path d="M2.5 0.5 H7.5 V3.5 H2.5 Z M0.5 4 H9.5 V8.5 H0.5 Z M2 9 H8 V9.8 H2 Z"/></svg>01-345-6789</li>
      <li><svg viewBox="0 0 10 10" aria-label="Email"><path d="M0.5 2 H9.5 V8 H0.5 Z M0.5 2 L5 5.5 L9.5 2" stroke="#fff" stroke-width="0.8"/></svg>info@meridobuild.com</li>
      <li><svg viewBox="0 0 10 10" aria-label="Website"><circle cx="5" cy="5" r="4.5"/><path d="M0.8 5 H9.2 M5 0.5 V9.5" stroke="#fff" stroke-width="0.7"/></svg>www.meridobuild.com</li>
    </ul>

    <svg class="swoosh" viewBox="0 0 525 298" aria-hidden="true">
      <defs>
        <linearGradient id="charcoal-fade" x1="0" y1="0" x2="1" y2="0">
          <stop offset="0" stop-color="#232323"/>
          <stop offset="0.55" stop-color="#3a3a3a"/>
          <stop offset="1" stop-color="#8a8a8a"/>
        </linearGradient>
      </defs>
      <path d="M0 252 C160 226 360 212 525 226 L525 298 L0 298 Z" fill="#1a4b7d"/>
      <path d="M0 252 C160 226 360 212 525 226" fill="none" stroke="#ffffff" stroke-width="2"/>
      <path d="M0 266 C110 262 220 252 330 238 C230 262 120 282 0 298 Z" fill="url(#charcoal-fade)"/>
      <path d="M0 264 C110 260 220 250 330 237" fill="none" stroke="#ffffff" stroke-width="2.5"/>
    </svg>

    <div class="holder">
      <div class="holder__name">Your Name</div>
      <div class="holder__title">Title</div>
    </div>
  </section>

  <section class="card card--back" aria-label="Business card back">
    <div class="wordmark">MERIDO</div>
    <div class="web-address">www.meridobuild.com</div>
  </section>
</body>
</html>
```